Building company buisness cards

We are looking for a sharp modern new look for our business cards.We are a New Zealand based company that specialises in house and land packages.We have attached a photo of the current logo and would like to see if it can be improved somehow if needed.We are open to any colours but we have chosen Black and White at this stage. Feel free to change the font and make the logo smarter looking.Play with the colours and see what looks best.We want a card that looks so good know one will want to throw it away!

Target Market(s)

Building profesonals, home buyers

Industry/Entity Type

Building

Contact Information for Business Card

Garrick Tenwood
0275390628
garrickt@hartvale.co.nz

Font styles to use
Serif
Sans Serif

Colors

Designer to choose colors to be used in the design.

Requirements
Must have
• Just the logo on one side and details on the other
• Clean simple looking card
Nice to have
• Round corners and detail like raised or spot UV
• Something that stands out
Should not have
• To title needed, Director etc

```html
<!DOCTYPE html>
<html lang="en">
<head>
<meta charset="UTF-8">
<title>Hartvale Business Cards</title>
<link rel="stylesheet" href="https://fonts.googleapis.com/css2?family=Oswald:wght@500&family=Work+Sans:wght@400;600&display=swap">
<style>
  :root {
    --backdrop: #1b1b1b;
    --card: #1e1e1e;
    --card-edge: #262626;
    --emboss: #101010;
    --emboss-light: rgba(255,255,255,0.05);
    --foil: #e6e6e6;
    --divider: #5a5a5a;
  }
  * { margin: 0; padding: 0; box-sizing: border-box; }
  html, body {
    width: 1200px; height: 900px; overflow: hidden;
    background: var(--backdrop);
  }
  .sheet {
    width: 1200px; height: 900px;
    display: flex; flex-direction: column;
    align-items: center; justify-content: center;
    gap: 50px;
  }
  .card {
    position: relative;
    width: 660px; height: 367px;
    background: var(--card);
    border: 1px solid var(--card-edge);
    border-radius: 10px;
  }
  /* Front */
  .card--front {
    display: flex; align-items: center; justify-content: center;
    gap: 22px;
  }
  .brand-name {
    font-family: "Work Sans", sans-serif;
    font-weight: 600;
    font-size: 70px;
    letter-spacing: 1px;
    color: var(--foil);
  }
  .brand-circle { width: 64px; height: 64px; }
  /* Back */
  .card--back { font-family: "Work Sans", sans-serif; }
  .identity {
    position: absolute; left: 62px; top: 112px;
    text-align: right; width: 240px;
  }
  .identity__name {
    font-family: "Oswald", sans-serif;
    font-weight: 500;
    font-size: 31px;
    letter-spacing: 1px;
    text-transform: uppercase;
    color: var(--emboss);
    text-shadow: 0 1px 0 var(--emboss-light);
    line-height: 1.1;
  }
  .identity__role {
    font-size: 16px;
    letter-spacing: 1px;
    color: var(--emboss);
    text-shadow: 0 1px 0 var(--emboss-light);
  }
  .divider {
    position: absolute; left: 325px; top: 112px;
    width: 1px; height: 82px;
    background: var(--divider);
  }
  .contacts {
    position: absolute; left: 350px; top: 118px;
    list-style: none;
  }
  .contacts li {
    display: flex; align-items: center; gap: 12px;
    font-size: 18px; letter-spacing: 0.5px;
    color: var(--foil);
    line-height: 24px;
  }
  .contacts svg { width: 12px; height: 12px; flex: none; }
  .address {
    position: absolute; left: 62px; bottom: 48px;
    font-size: 18px; font-weight: 600; letter-spacing: 1px;
    color: var(--emboss);
    text-shadow: 0 1px 0 var(--emboss-light);
  }
</style>
</head>
<body>
<main class="sheet">
  <section class="card card--front" aria-label="Card front">
    <span class="brand-name">Hartvale</span>
    <svg class="brand-circle" viewBox="0 0 64 64" aria-hidden="true">
      <circle cx="32" cy="32" r="29" fill="none" stroke="var(--foil)" stroke-width="3"/>
    </svg>
  </section>

  <section class="card card--back" aria-label="Card back">
    <div class="identity">
      <p class="identity__name">Garrick Tenwood</p>
      <p class="identity__role">Director</p>
    </div>
    <span class="divider"></span>
    <ul class="contacts">
      <li>
        <svg viewBox="0 0 12 12" aria-hidden="true"><path d="M2.5 1h2l1 2.5-1.3 1a6 6 0 0 0 3.3 3.3l1-1.3 2.5 1v2a1 1 0 0 1-1 1A9 9 0 0 1 1.5 2a1 1 0 0 1 1-1z" fill="var(--foil)"/></svg>
        0275390628
      </li>
      <li>
        <svg viewBox="0 0 12 12" aria-hidden="true"><rect x="0.8" y="2.3" width="10.4" height="7.4" fill="none" stroke="var(--foil)" stroke-width="1.2"/><path d="M1 2.6l5 4 5-4" fill="none" stroke="var(--foil)" stroke-width="1.2"/></svg>
        garrickt@hartvale.co.nz
      </li>
      <li>
        <svg viewBox="0 0 12 12" aria-hidden="true"><circle cx="6" cy="6" r="5" fill="none" stroke="var(--foil)" stroke-width="1.1"/><ellipse cx="6" cy="6" rx="2.2" ry="5" fill="none" stroke="var(--foil)" stroke-width="1"/><path d="M1 6h10" stroke="var(--foil)" stroke-width="1"/></svg>
        www.hartvale.co.nz
      </li>
    </ul>
    <p class="address">142b Marlow Street, Ashbury, NZ, 7021</p>
  </section>
</main>
</body>
</html>
```